New business card for a regional office of a US M&A company

We need business card for a finance company, office based in Hong Kong , our Head office is in US, our business is to Merge and acquires companies , the new office will be a regional office for the Asia Pacific region. We want to use the head office logo as attached ( but don't have to be exactly the same, can be a variation to it) as a base and then add Asia Pacific alongside the logo.
We would prefer to have be bilingual Eng + Chinese, although we don't really have Chinese company name .

Industry/Entity Type

Business

Contact Information for Business Card

Clara Jo Tsang
 

VP,
APAC M&A Operations
ORIN VANTAGE Asia Pacific Limited
 
Unit 1407, K18
18 Tai Lok Shan Road, 
Hong Kong 
 
M: +852 6038 1742
T : +852 2836 4100
F : +852 2836 4177
VOIP: 4158
 
cjtsang@orinvantage.com

Font styles to use
Serif
Sans Serif

Colors

Designer to choose colors to be used in the design.

Requirements
Must have
• APAC Office

```html
<!DOCTYPE html>
<html lang="en">
<head>
<meta charset="UTF-8">
<title>Orin Vantage – Business Card</title>
<link href="https://fonts.googleapis.com/css2?family=Open+Sans:wght@400;600;700;800&display=swap" rel="stylesheet">
<style>
  :root {
    --backdrop: #2a2a2a;
    --card: #1b1b1c;
    --card-edge: #262627;
    --accent: #1fb0cc;
    --ink: #f2f2f2;
    --ink-soft: #d6d6d6;
    --emboss: #6e6e70;
  }
  * { margin: 0; padding: 0; box-sizing: border-box; }
  html, body { width: 1200px; height: 930px; overflow: hidden; }
  body {
    background: var(--backdrop);
    font-family: "Open Sans", Arial, sans-serif;
    position: relative;
  }
  .card {
    position: absolute;
    width: 560px;
    height: 320px;
    border-radius: 16px;
    background: linear-gradient(135deg, var(--card-edge), var(--card) 60%);
    box-shadow: 0 18px 40px rgba(0,0,0,.45);
    overflow: hidden;
  }
  .card--front { left: 140px; top: 90px; }
  .card--back { left: 500px; top: 510px; }

  /* Front */
  .front-brand {
    position: absolute;
    left: 0; right: 0; top: 0; bottom: 0;
    display: flex; align-items: center; justify-content: center; gap: 16px;
  }
  .brand-square {
    width: 44px; height: 44px;
    background: var(--emboss);
  }
  .front-brand .brand-name {
    font-weight: 800; font-size: 40px; letter-spacing: 1px;
    color: var(--emboss);
  }

  /* Back */
  .back-brand {
    position: absolute; left: 34px; top: 90px; width: 220px;
    display: flex; flex-direction: column; align-items: flex-start; gap: 16px;
  }
  .back-brand .brand-square {
    width: 52px; height: 52px; margin-left: 66px;
    background: #ffffff;
  }
  .back-brand .brand-name {
    font-weight: 800; font-size: 30px; line-height: 1.05;
    color: var(--accent); letter-spacing: .5px;
  }
  .divider {
    position: absolute; left: 268px; top: 70px;
    width: 2px; height: 150px; background: var(--accent);
  }
  .contact {
    position: absolute; left: 290px; top: 64px; width: 250px;
  }
  .person-name {
    color: var(--accent); font-weight: 600; font-size: 22px; line-height: 1.15;
  }
  .person-title {
    color: var(--ink); font-weight: 700; font-size: 12px; margin-bottom: 16px;
  }
  .contact-list { list-style: none; }
  .contact-list li {
    display: flex; align-items: center; gap: 10px;
    color: var(--ink-soft); font-size: 13px; line-height: 1.55;
  }
  .contact-list svg { width: 11px; height: 11px; fill: var(--accent); flex: none; }
  .address {
    position: absolute; left: 34px; right: 20px; bottom: 28px;
    color: var(--ink-soft); font-size: 13px;
  }
</style>
</head>
<body>

<section class="card card--front" aria-label="Card front">
  <div class="front-brand">
    <span class="brand-square"></span>
    <span class="brand-name">ORIN VANTAGE</span>
  </div>
</section>

<section class="card card--back" aria-label="Card back">
  <div class="back-brand">
    <span class="brand-square"></span>
    <span class="brand-name">ORIN VANTAGE</span>
  </div>

  <div class="divider"></div>

  <div class="contact">
    <p class="person-name">Clara Jo Tsang</p>
    <p class="person-title">VP, APAC M&amp;A Operations</p>
    <ul class="contact-list">
      <li>
        <svg viewBox="0 0 12 12" aria-hidden="true"><path d="M3 0h6a1 1 0 0 1 1 1v10a1 1 0 0 1-1 1H3a1 1 0 0 1-1-1V1a1 1 0 0 1 1-1zm0 1.5v8h6v-8z"/></svg>
        +852 6038 1742
      </li>
      <li>
        <svg viewBox="0 0 12 12" aria-hidden="true"><path d="M2.5 0.5l2 2.2-1 1.3c.7 1.6 2 2.9 3.5 3.6l1.3-1 2.2 2-1.2 2.2C5 10.5 1.5 7 0.3 1.7z"/></svg>
        +852 2836 4100
      </li>
      <li>
        <svg viewBox="0 0 12 12" aria-hidden="true"><path d="M3 0h5v3H3zM1 4h10v6H9v2H3v-2H1zm3 4v3h4V8z"/></svg>
        +852 2836 4177
      </li>
      <li>
        <svg viewBox="0 0 12 12" aria-hidden="true"><path d="M0 2h12v1.2L6 7 0 3.2zM0 4.6l6 3.8 6-3.8V10H0z"/></svg>
        cjtsang@orinvantage.com
      </li>
    </ul>
  </div>

  <p class="address">Unit 1407, K18 18 Tai Lok Shan Road, Hong Kong</p>
</section>

</body>
</html>
```